Stonebrace Business Card Design

The Stonebrace Co is an aggregate (crushing) equipment dealer serving Western Canadian provinces. Stonebrace is a distributor of aggregate equipment for different manufacturers.

We are looking to change and update the existing business card which has been used since the existence of the company. A copy of existing card has been attached for reference. The Stonebrace Co logo we want to remain the same and we want the green color to remain the same.

We are wanting something new with a different look. A refreshing card to show a new modern and updated look. No longer wanting to have the manufacturers on the back of the card but something more like our logo on the back of the card with a statement like "Quarry Equipment"

ideas could be:
- card can be different colors on front and back
- front or reverse of the card could possibly be the green color with the logo in black

Target Market(s)

Owners of Aggregate/Crushing companies

Contact Information for Business Card

see above

Requirements
Must have
• - logo to remain same along with same font within logo
• - green color to remain same
Nice to have
• as noted above under project description
Should not have

```html
<!DOCTYPE html>
<html lang="en">
<head>
<meta charset="utf-8">
<title>Stonebrace Business Card</title>
<link href="https://fonts.googleapis.com/css2?family=Arimo:wght@400;700&display=swap" rel="stylesheet">
<style>
  :root {
    --stage: #e4e1dd;
    --brand-green: #8a8c0a;
    --ink-black: #1f1d1e;
    --paper-grey: #eeeeee;
    --white: #ffffff;
    --text-dark: #2a2a2a;
  }
  html, body {
    margin: 0;
    padding: 0;
    width: 1200px;
    height: 900px;
    overflow: hidden;
    background: var(--stage);
    font-family: "Arimo", Arial, sans-serif;
  }
  .canvas {
    position: relative;
    width: 1200px;
    height: 900px;
  }
  .card {
    position: absolute;
    overflow: hidden;
    box-shadow: 0 6px 18px rgba(0,0,0,0.18);
  }

  /* Front */
  .card-front {
    left: 77px;
    top: 34px;
    width: 588px;
    height: 364px;
    background: var(--brand-green);
    color: var(--white);
  }
  .front-band {
    position: absolute;
    left: 0;
    top: 0;
    width: 220px;
    height: 100%;
    background: var(--ink-black);
  }
  .contact-block {
    position: absolute;
    right: 37px;
    top: 58px;
    text-align: right;
  }
  .holder-name {
    margin: 0 0 70px;
    font-size: 21px;
    font-weight: 400;
    letter-spacing: 0.5px;
  }
  .contact-list {
    list-style: none;
    margin: 0;
    padding: 0;
    font-size: 16px;
    line-height: 21.5px;
  }
  .contact-list li {
    display: flex;
    justify-content: flex-end;
    align-items: center;
    gap: 3px;
  }
  .contact-list svg {
    width: 12px;
    height: 12px;
    fill: var(--white);
  }
  .address {
    margin: 22px 0 0;
    font-size: 16px;
    line-height: 21.5px;
    font-style: normal;
  }

  /* Back */
  .card-back {
    left: 388px;
    top: 505px;
    width: 566px;
    height: 352px;
    background: var(--paper-grey);
  }
  .brand-mark {
    position: absolute;
    left: 0;
    right: 0;
    top: 118px;
    text-align: center;
  }
  .brand-dot {
    display: block;
    width: 40px;
    height: 40px;
    margin: 0 auto 34px;
    border-radius: 50%;
    background: var(--brand-green);
  }
  .brand-name {
    margin: 0;
    font-size: 23px;
    font-weight: 700;
    color: var(--ink-black);
    letter-spacing: 0.3px;
  }
  .tagline {
    position: absolute;
    left: 40px;
    right: 38px;
    top: 265px;
    display: flex;
    align-items: center;
    gap: 4px;
    font-size: 16px;
    font-weight: 700;
    color: #3a3a3a;
    letter-spacing: 0.3px;
  }
  .tagline-rule {
    flex: 1;
    height: 1px;
    background: var(--brand-green);
  }
</style>
</head>
<body>
<main class="canvas">

  <section class="card card-front" aria-label="Business card front">
    <div class="front-band"></div>
    <div class="contact-block">
      <h1 class="holder-name">DALE HARMON</h1>
      <ul class="contact-list">
        <li>780.555.0142(Direct)
          <svg viewBox="0 0 12 12" aria-hidden="true"><path d="M1 4c0-2 2-3 5-3s5 1 5 3l-2 1-1-1.5H4L3 5zM2 6h8l1 5H1z"/></svg></li>
        <li>780.555.0187
          <svg viewBox="0 0 12 12" aria-hidden="true"><path d="M1 4c0-2 2-3 5-3s5 1 5 3l-2 1-1-1.5H4L3 5zM2 6h8l1 5H1z"/></svg></li>
        <li>780.555.0163
          <svg viewBox="0 0 12 12" aria-hidden="true"><path d="M1 4h2V1h6v3h2v7H1zM4 2v2h4V2zM3 6v1h2V6zm3 0v1h2V6zM3 8v1h2V8zm3 0v1h2V8z"/></svg></li>
        <li>dale@stonebr.com
          <svg viewBox="0 0 12 12" aria-hidden="true"><path d="M0 2h12v8H0zM1 3l5 4 5-4z" fill-rule="evenodd"/></svg></li>
        <li>www.stonebrace.ca
          <svg viewBox="0 0 12 12" aria-hidden="true"><circle cx="6" cy="6" r="5.5"/></svg></li>
      </ul>
      <address class="address">2210-48B Avenue<br>Brookvale, Alberta T0B 3K8</address>
    </div>
  </section>

  <section class="card card-back" aria-label="Business card back">
    <div class="brand-mark">
      <span class="brand-dot" aria-hidden="true"></span>
      <p class="brand-name">THE STONEBRACE CO.</p>
    </div>
    <div class="tagline">
      <span class="tagline-rule"></span>
      <span class="tagline-text">QUARRY EQUIPMENT</span>
      <span class="tagline-rule"></span>
    </div>
  </section>

</main>
</body>
</html>
```